Automotive component supplier needs a business card design

We need a business card design for our company called Velran Global Components Ltd based in the UK. We are a supplier of interior and exterior components to premium car manufacturers such as Corvel Ashby, Hadley Fenn, Marquist and Tavarelli. We would like to see a modern business card design that uses the colour blue.

Target Market(s)

Premium automotive car manufacturers.

Industry/Entity Type

Automotive

Contact Information for Business Card

Company Name : Velran Global Components Limited
Address: 17 Marlow Yard, Upper Heath, Warwick, CV31 8QL, United Kingdom
Web Address : www.velrancomponents-example.co.uk

Font styles to use
Other font styles liked:
• Helvetica

Colors
3176b5
0255a3
85acd3
cfdeed
cee9f5
85cae6
34a6d7
0692cd
9bcb3c

Requirements
Must have
• Clear company logo and a mixture of blue colours.
Nice to have
• A high quality modern image.
Should not have
• Multiple colours.

```html
<!DOCTYPE html>
<html lang="en">
<head>
<meta charset="utf-8">
<title>Velran Global Components – Business Card</title>
<link href="https://fonts.googleapis.com/css2?family=Lato:wght@400;700;900&display=swap" rel="stylesheet">
<style>
  :root {
    --brand-blue: #0692cd;
    --accent-green: #9bcb3c;
    --card-white: #ffffff;
    --ink: #1e1e1e;
    --backdrop: #e4e7ea;
  }
  * { box-sizing: border-box; margin: 0; padding: 0; }
  html, body {
    width: 1200px; height: 800px; overflow: hidden;
    background: var(--backdrop);
    font-family: "Lato", Helvetica, Arial, sans-serif;
  }
  .canvas { position: relative; width: 1200px; height: 800px; }

  .card {
    position: absolute;
    width: 600px; height: 343px;
    border-radius: 4px;
    box-shadow: 0 10px 28px rgba(0,0,0,.18);
    overflow: hidden;
  }

  .logo-name {
    font-weight: 900; text-transform: uppercase;
    line-height: 1; white-space: nowrap;
  }

  /* Front */
  .card--front { left: 70px; top: 45px; background: var(--brand-blue); }
  .front-logo {
    position: absolute; left: 0; right: 0; top: 118px;
    text-align: center;
  }
  .front-logo .logo-name { color: var(--card-white); font-size: 30px; letter-spacing: .5px; }
  .front-web {
    position: absolute; left: 0; right: 0; bottom: 44px;
    text-align: center; color: var(--card-white);
    font-size: 15px; letter-spacing: 1.6px; white-space: nowrap;
  }

  /* Back */
  .card--back { left: 530px; top: 410px; background: var(--card-white); }
  .back-rule {
    position: absolute; left: 26px; top: 0; bottom: 0;
    width: 3px; background: var(--accent-green);
  }
  .back-panel {
    position: absolute; left: 29px; top: 0; bottom: 0; width: 250px;
    background: var(--brand-blue);
    padding: 40px 0 0 34px;
  }
  .person-name { color: var(--accent-green); font-weight: 700; font-size: 25px; white-space: nowrap; }
  .person-role { color: var(--card-white); font-size: 16px; margin-top: 4px; }

  .back-logo {
    position: absolute; right: 26px; top: 38px;
    text-align: right;
  }
  .back-logo .logo-name { color: var(--brand-blue); font-size: 15.5px; letter-spacing: .3px; }

  .contact {
    position: absolute; left: 306px; top: 128px; right: 16px;
    color: var(--ink); font-size: 14.5px; line-height: 1.38;
  }
  .contact-address { margin-bottom: 14px; white-space: nowrap; }
  .contact-list { list-style: none; }
  .contact-list li {
    display: flex; align-items: center; gap: 9px;
    font-size: 13.5px; line-height: 1.5; white-space: nowrap;
  }
  .contact-list svg { width: 13px; height: 13px; flex: none; fill: var(--brand-blue); }
</style>
</head>
<body>
<main class="canvas">

  <section class="card card--front" aria-label="Business card front">
    <div class="front-logo">
      <span class="logo-name">Velran Global Components</span>
    </div>
    <p class="front-web">www.velrancomponents-example.co.uk</p>
  </section>

  <section class="card card--back" aria-label="Business card back">
    <div class="back-rule"></div>
    <div class="back-panel">
      <p class="person-name">Maren Holloway</p>
      <p class="person-role">Manager</p>
    </div>

    <div class="back-logo">
      <span class="logo-name">Velran Global Components</span>
    </div>

    <div class="contact">
      <p class="contact-address">17 Marlow Yard, Upper Heath<br>Warwick, CV31 8QL<br>United Kingdom</p>
      <ul class="contact-list">
        <li>
          <svg viewBox="0 0 24 24" aria-hidden="true"><path d="M6.6 10.8a15.1 15.1 0 0 0 6.6 6.6l2.2-2.2a1 1 0 0 1 1-.25 11.4 11.4 0 0 0 3.6.57 1 1 0 0 1 1 1V20a1 1 0 0 1-1 1A17 17 0 0 1 3 4a1 1 0 0 1 1-1h3.5a1 1 0 0 1 1 1c0 1.25.2 2.45.57 3.6a1 1 0 0 1-.25 1z"/></svg>
          512 040 7300
        </li>
        <li>
          <svg viewBox="0 0 24 24" aria-hidden="true"><path d="M7 1h10a2 2 0 0 1 2 2v18a2 2 0 0 1-2 2H7a2 2 0 0 1-2-2V3a2 2 0 0 1 2-2zm0 3v14h10V4zm5 15.5a1 1 0 1 0 0 2 1 1 0 0 0 0-2z"/></svg>
          512 040 7301
        </li>
        <li>
          <svg viewBox="0 0 24 24" aria-hidden="true"><path d="M2 5h20v14H2zm2 2v.5l8 5 8-5V7zm0 2.8V17h16V9.8l-8 5z"/></svg>
          info@velrancomponents-example.co.uk
        </li>
        <li>
          <svg viewBox="0 0 24 24" aria-hidden="true"><path d="M12 2a10 10 0 1 0 0 20 10 10 0 0 0 0-20zm6.9 9h-3a15 15 0 0 0-1.3-5.9A8 8 0 0 1 18.9 11zM12 4.1c.9 1.2 1.8 3.6 1.9 6.9h-3.8c.1-3.3 1-5.7 1.9-6.9zM9.4 5.1A15 15 0 0 0 8.1 11h-3a8 8 0 0 1 4.3-5.9zM5.1 13h3a15 15 0 0 0 1.3 5.9A8 8 0 0 1 5.1 13zm6.9 6.9c-.9-1.2-1.8-3.6-1.9-6.9h3.8c-.1 3.3-1 5.7-1.9 6.9zm2.6-1a15 15 0 0 0 1.3-5.9h3a8 8 0 0 1-4.3 5.9z"/></svg>
          www.velrancomponents-example.co.uk
        </li>
      </ul>
    </div>
  </section>

</main>
</body>
</html>
```